wardrobe/costume stylist needs good business card for own business

Hi:)

I'm wanting a business card for my company. I am a freelance stylist.

I do wardrobe/costume stylist to TV commercials; Films; Fashion and Lifestyle shoots.

I'd like a design based around my name Rosalind Parfrey written nicely, maybe a colour? Up to you?!

I've attached a couple of images of business cards I like
.... be creative and have fun!

Thank you :)

Reason: I was trying to get my new business card ready for before I headed overseas Friday morning but I don't think that was realistic so I'd like to extend the deadline to give time to the project. Thank you

Hi designers:) Thank you for all your designs, I've extended the deadline until Sunday, so there's a bit more time. I've attached 3 pictures of business cards which I quite like, please take a look to see if it can be of help in your process. I like the pale plain or patterned background with dark font and the dark plain or patterned background with the pale font the motifs the feminine fonts the plain fonts I like the idea of playing with a circle or some shape on one side of the card with my name or initials as in the picture I have on my post could you play around with this idea a bit please? Thank you all for the work you've done :) Rosa

Hi I am working overseas til Saturday night sorry for no feedback until I teturn Thanks :) Rosa

Hi designers, Thank you all so much for submitting your designs, I really appreciate your input into my project :) I'm sorry I didn't get to respond to some comments, and give feedback. I didn't back from being away until later than I expected, and the deadline had passed then, so apologies. Thanks to you all again for all your really good designs :) Rosa

Target Market(s)

I am a freelance stylist my target audience is producers, production companies, photographers, directors...

Industry/Entity Type

Business

Requirements
Must have
• Rosalind Parfrey
Stylist or Wardrobe Stylist

email rosaparfrey@mailbox-example.co.nz
Mobile 0218467193

(Don't have to use the words 'email' and 'mobile')
Nice to have
• Would like it to be double sided
Like B & W
Like pale colour background with dark font or white font
Like dark colour background with pale font
Should not have
• I would prefer it not to incorporate pictures

```html
<!DOCTYPE html>
<html lang="en">
<head>
<meta charset="utf-8">
<title>Rosalind Parfrey — Wardrobe Stylist Business Card</title>
<link href="https://fonts.googleapis.com/css2?family=Yellowtail&family=Archivo:wght@400;800&display=swap" rel="stylesheet">
<style>
  :root {
    --stage: #1f1f22;
    --cyan: #8cfaf8;
    --magenta: #ff00e0;
    --ink: #111111;
    --white: #ffffff;
    --mark: #2b2b2e;
  }
  * { margin: 0; padding: 0; box-sizing: border-box; }
  html, body { width: 1200px; height: 533px; overflow: hidden; }
  body {
    background: var(--stage);
    display: flex;
    align-items: center;
    justify-content: space-between;
    padding: 0 20px;
  }
  .card {
    position: relative;
    width: 560px;
    height: 320px;
    overflow: hidden;
  }
  .card--front { background: var(--cyan); }
  .card--back { background: var(--magenta); }

  .front-band {
    position: absolute;
    left: 0; right: 0;
    top: 99px;
    height: 58px;
    background: var(--magenta);
    display: flex;
    align-items: center;
    padding-left: 22px;
    gap: 14px;
  }
  .name-mark {
    width: 40px; height: 40px;
    border-radius: 50%;
    background: var(--mark);
    flex: none;
  }
  .name-script {
    font-family: "Yellowtail", cursive;
    font-size: 38px;
    color: var(--white);
    line-height: 1;
  }
  .contact {
    position: absolute;
    left: 330px;
    top: 164px;
    color: var(--ink);
    font-family: "Archivo", Arial, sans-serif;
  }
  .contact__name {
    font-weight: 800;
    font-size: 18px;
    letter-spacing: -0.3px;
    line-height: 1;
  }
  .contact__role {
    font-weight: 800;
    font-size: 9.5px;
    margin-top: 3px;
    letter-spacing: -0.1px;
  }
  .contact__line {
    display: flex;
    align-items: center;
    gap: 8px;
    margin-top: 8px;
    font-size: 13px;
    font-weight: 400;
  }
  .contact__line:first-of-type { margin-top: 12px; }
  .contact__icon {
    width: 24px; height: 24px;
    background: var(--magenta);
    flex: none;
  }
  .back-art { display: block; width: 100%; height: 100%; }
  .back-script {
    font-family: "Yellowtail", cursive;
    font-size: 38px;
    fill: var(--white);
  }
</style>
</head>
<body>

  <section class="card card--front" aria-label="Card front">
    <div class="front-band">
      <span class="name-mark"></span>
      <span class="name-script">Rosalind Parfrey</span>
    </div>
    <div class="contact">
      <p class="contact__name">ROSALIND PARFREY</p>
      <p class="contact__role">WARDROBE STYLIST</p>
      <p class="contact__line">
        <svg class="contact__icon" viewBox="0 0 24 24" aria-hidden="true">
          <rect width="24" height="24" fill="var(--magenta)"/>
          <rect x="4" y="6.5" width="16" height="11" fill="none" stroke="var(--white)" stroke-width="1.6"/>
          <polyline points="4,6.5 12,13 20,6.5" fill="none" stroke="var(--white)" stroke-width="1.6"/>
        </svg>
        <span>rosaparfrey@mailbox-example.co.nz</span>
      </p>
      <p class="contact__line">
        <svg class="contact__icon" viewBox="0 0 24 24" aria-hidden="true">
          <rect width="24" height="24" fill="var(--magenta)"/>
          <rect x="7.5" y="3.5" width="9" height="17" rx="1.5" fill="none" stroke="var(--white)" stroke-width="1.6"/>
          <circle cx="12" cy="17.5" r="1" fill="var(--white)"/>
        </svg>
        <span>0218467193</span>
      </p>
    </div>
  </section>

  <section class="card card--back" aria-label="Card back">
    <svg class="back-art" viewBox="0 0 560 320">
      <polygon points="0,157 560,112 560,186 0,231" fill="var(--cyan)"/>
      <g transform="rotate(-4.6 280 171)">
        <circle cx="150" cy="172" r="20" fill="var(--mark)"/>
        <text class="back-script" x="184" y="184">Rosalind Parfrey</text>
      </g>
    </svg>
  </section>

</body>
</html>
```